VL Business Card

Used Car Sales
We are trying to recreate the image of our license plate on business cards,
it is a red background with a white oval that is open on the ends
I attempted to upload the image but it was a dismal failure when the products arrived
the lettering was too small and the edges were white
I think maybe the red needs some texture in it, still red but something that doesn't look so flat
and maybe a beveled edge around the white (not sure)

Target Market(s)

Adults 25-65 that drive

Industry/Entity Type

Business

Contact Information for Business Card

Danielle Hargrove, Sales Manager, FAIRVIEW AUTO SALES, INC., 462 Birch Lane, Pulaski, TN 38491,
931 555-0172 (office), 931 555-0186 (fax) - We Finance everyone with approved credit
FairviewAutoSales.Example

On Back: Financing Available - We Finance everyone with approved credit
Easy Payments: Monthly, Semi-Monthly or Weekly
Ask about our Layaway plan
Open Mon-Sat
8:30 AM - 5 PM

Requirements
Must have
• We want to match the license plate (minus holes for screws)

```html
<!DOCTYPE html>
<html lang="en">
<head>
<meta charset="utf-8">
<title>VL Business Card</title>
<link rel="stylesheet" href="https://fonts.googleapis.com/css2?family=Arimo:wght@400;700&display=swap">
<style>
  :root {
    --page-bg: #e8e5e2;
    --card-white: #ffffff;
    --ink-dark: #3d3d3d;
    --ink-soft: #5a5a5a;
    --red-deep: #bd1c28;
    --red-mid: #d4434d;
    --red-base: #c8303b;
    --link-red: #d0252f;
  }
  * { box-sizing: border-box; margin: 0; padding: 0; }
  html, body {
    width: 1200px; height: 914px; overflow: hidden;
    background: var(--page-bg);
    font-family: "Arimo", Arial, sans-serif;
  }
  .sheet {
    width: 1200px; height: 914px;
    display: flex; flex-direction: column;
    align-items: center; justify-content: center; gap: 56px;
  }
  .card {
    position: relative;
    width: 620px; height: 354px;
    background: var(--card-white);
    overflow: hidden;
    box-shadow: 0 6px 18px rgba(0,0,0,0.18);
  }
  .card-swoosh { position: absolute; inset: 0; width: 100%; height: 100%; }
  .card-text {
    position: relative;
    text-align: center;
    color: var(--ink-dark);
  }
  /* front */
  .front .card-text { padding-top: 46px; }
  .person-name {
    font-weight: 700; font-size: 24px; letter-spacing: 0.5px;
    text-transform: uppercase; color: var(--ink-dark);
  }
  .person-title { font-size: 15px; color: var(--ink-soft); margin-top: 2px; }
  .company-name {
    font-weight: 700; font-size: 20px; letter-spacing: 0.5px;
    text-transform: uppercase; margin-top: 20px;
  }
  .contact-line { font-size: 15px; line-height: 19px; }
  .tagline { font-size: 15px; margin-top: 10px; }
  .web-address { font-size: 17px; color: var(--link-red); }
  /* back */
  .back .card-text { padding-top: 52px; font-size: 17px; line-height: 21px; }
  .back-group + .back-group { margin-top: 20px; }
</style>
</head>
<body>
<main class="sheet">

  <section class="card front" aria-label="Business card front">
    <svg class="card-swoosh" viewBox="0 0 620 354" preserveAspectRatio="none" aria-hidden="true">
      <defs>
        <linearGradient id="redFront" x1="0" y1="0" x2="1" y2="0">
          <stop offset="0" stop-color="var(--red-base)"/>
          <stop offset="0.4" stop-color="var(--red-mid)"/>
          <stop offset="1" stop-color="var(--red-deep)"/>
        </linearGradient>
      </defs>
      <rect width="620" height="354" fill="url(#redFront)"/>
      <path d="M0 0 H620 V318 C430 345 150 300 0 150 Z" fill="var(--card-white)"/>
    </svg>
    <div class="card-text">
      <h1 class="person-name">Danielle Hargrove</h1>
      <p class="person-title">Sales Manager</p>
      <h2 class="company-name">Fairview Auto Sales, Inc.</h2>
      <p class="contact-line">462 Birch Lane, Pulaski, TN 38491</p>
      <p class="contact-line">931 555-0172 (office)</p>
      <p class="contact-line">931 555-0186 (fax)</p>
      <p class="tagline">We Finance everyone with approved credit</p>
      <p class="web-address">FairviewAutoSales.Example</p>
    </div>
  </section>

  <section class="card back" aria-label="Business card back">
    <svg class="card-swoosh" viewBox="0 0 620 354" preserveAspectRatio="none" aria-hidden="true">
      <defs>
        <linearGradient id="redBack" x1="0" y1="0" x2="1" y2="0">
          <stop offset="0" stop-color="var(--red-base)"/>
          <stop offset="0.4" stop-color="var(--red-mid)"/>
          <stop offset="1" stop-color="var(--red-deep)"/>
        </linearGradient>
      </defs>
      <rect width="620" height="354" fill="url(#redBack)"/>
      <path d="M0 0 H620 V262 C430 290 170 262 0 150 Z" fill="var(--card-white)"/>
    </svg>
    <div class="card-text">
      <div class="back-group">
        <p>Financing Available</p>
        <p>We Finance everyone with approved credit</p>
        <p>Easy Payments: Monthly, Semi-Monthly or Weekly</p>
      </div>
      <div class="back-group">
        <p>Ask about our Layaway plan</p>
      </div>
      <div class="back-group">
        <p>Open Mon-Sat</p>
        <p>8:30 AM - 5 PM</p>
      </div>
    </div>
  </section>

</main>
</body>
</html>
```